Marlowe Crest Realty business card design

Looking for an upscale and clean business card design and updated logo. I sell to a very high-end south Florida real estate market.
Target Market(s)
High-end real estate in south Florida real estate market
Industry/Entity Type
Real Estate Agent
Contact Information for Business Card
Marlowe Crest Realty, Inc
738 West Pinecrest Ave, Suite 410/510, Fort Lauderdale, FL 33308
Gary Whitlock - Broker/Owner
954-327-8846 Direct
garyshomes@quellmail.com
Website: DwellTarrowBay.com
Font styles to use
Other font styles liked:
- Copperplate Gothic, Georgia, etc.
Requirements
Must have
- My photo, company name, my name and title, all info stated in Details above
Nice to have
- Luxury home design element, waterfront

```html
<!DOCTYPE html>
<html lang="en">
<head>
<meta charset="utf-8">
<title>Marlowe Crest Realty – Business Card</title>
<link rel="stylesheet" href="https://fonts.googleapis.com/css2?family=Cinzel:wght@400;600;700&family=Tinos&display=swap">
<style>
  :root {
    --canvas-bg: #cfcfcf;
    --card-bg: #2a2a2a;
    --card-edge: #f2b318;
    --accent: #f5b61a;
    --text-light: #d9d9d9;
    --text-muted: #bdbdbd;
    --photo-tone-a: #9aa3b3;
    --photo-tone-b: #d8d8d6;
  }
  * { margin: 0; padding: 0; box-sizing: border-box; }
  html, body { width: 1200px; height: 800px; overflow: hidden; }
  body {
    background: var(--canvas-bg);
    font-family: "Cinzel", "Georgia", serif;
    position: relative;
  }
  .card {
    position: absolute;
    background: var(--card-bg);
    border-radius: 26px;
    box-shadow: 0 3px 0 var(--card-edge), 0 16px 30px rgba(0,0,0,0.25);
  }
  /* Front */
  .card-front {
    left: 110px; top: 110px;
    width: 340px; height: 580px;
    display: flex; flex-direction: column; align-items: center;
    text-align: center;
    padding-top: 62px;
  }
  .portrait {
    width: 150px; height: 150px;
    border-radius: 50%;
    border: 3px solid var(--accent);
    background: linear-gradient(135deg, var(--photo-tone-b) 0%, var(--photo-tone-a) 100%);
  }
  .agent-name {
    margin-top: 26px;
    color: var(--accent);
    font-size: 27px;
    font-weight: 700;
    letter-spacing: 1px;
  }
  .agent-title {
    margin-top: 4px;
    color: var(--text-light);
    font-size: 13px;
    letter-spacing: 1.5px;
  }
  .divider {
    width: 34px; height: 2px;
    background: var(--accent);
    margin: 22px 0 20px;
  }
  .address {
    color: var(--text-light);
    font-size: 12.5px;
    line-height: 1.45;
    letter-spacing: 0.8px;
    font-style: normal;
  }
  .address .company { font-weight: 700; }
  .contact-icons {
    display: flex; gap: 7px;
    margin: 20px 0 14px;
  }
  .contact-icons svg { width: 20px; height: 20px; display: block; }
  .contact-lines {
    color: var(--text-light);
    font-size: 12.5px;
    line-height: 1.5;
    letter-spacing: 0.8px;
  }
  /* Back */
  .card-back {
    left: 520px; top: 230px;
    width: 580px; height: 350px;
    display: flex; align-items: center; justify-content: center; gap: 18px;
  }
  .brand-dot {
    width: 46px; height: 46px;
    border-radius: 50%;
    background: var(--accent);
    flex: none;
  }
  .brand-name {
    color: var(--text-muted);
    font-family: "Tinos", "Georgia", serif;
    font-size: 34px;
    letter-spacing: 1px;
  }
</style>
</head>
<body>
  <section class="card card-front">
    <div class="portrait" role="img" aria-label="Portrait photo of Gary Whitlock"></div>
    <h1 class="agent-name">Gary Whitlock</h1>
    <p class="agent-title">Broker/Owner</p>
    <div class="divider"></div>
    <address class="address">
      <span class="company">Marlowe Crest Realty, Inc</span><br>
      738 West Pinecrest Ave<br>
      Suite 410/510<br>
      Fort Lauderdale<br>
      FL 33308
    </address>
    <div class="contact-icons">
      <svg viewBox="0 0 20 20" aria-label="Phone" role="img">
        <circle cx="10" cy="10" r="10" fill="var(--accent)"/>
        <path d="M7 5.5l1.6 2.2-1 1.2a6 6 0 0 0 3.5 3.5l1.2-1 2.2 1.6-1 1.6c-4 0-7.6-3.6-7.6-7.6z" fill="var(--card-bg)"/>
      </svg>
      <svg viewBox="0 0 20 20" aria-label="Email" role="img">
        <circle cx="10" cy="10" r="10" fill="var(--accent)"/>
        <rect x="5" y="6.5" width="10" height="7" fill="var(--card-bg)"/>
        <path d="M5 6.5l5 4 5-4" stroke="var(--accent)" stroke-width="1" fill="none"/>
      </svg>
      <svg viewBox="0 0 20 20" aria-label="Website" role="img">
        <circle cx="10" cy="10" r="10" fill="var(--accent)"/>
        <circle cx="10" cy="10" r="5" fill="none" stroke="var(--card-bg)" stroke-width="1.4"/>
        <path d="M5 10h10M10 5c-2.2 2.8-2.2 7.2 0 10M10 5c2.2 2.8 2.2 7.2 0 10" fill="none" stroke="var(--card-bg)" stroke-width="1.1"/>
      </svg>
    </div>
    <p class="contact-lines">
      954-327-8846<br>
      garyshomes@quellmail.com<br>
      DwellTarrowBay.com
    </p>
  </section>

  <section class="card card-back">
    <span class="brand-dot"></span>
    <span class="brand-name">Marlowe Crest Realty, Inc.</span>
  </section>
</body>
</html>
```